ambitious event and festival agency from austria needs fresh business card design

A new design is due for the new headquarters and the new challenges. We organize events for different target groups from 16 to 60 years. The design should therefore be straightforward and not confused, so we are open to new colors and the logo may also be changed. In general, however, the most interesting suggestions are the most interesting ones. after this order we are looking for more graphics for quellvanto facebook instagramm homepage etc A new design is due for the new headquarters and the new challenges. We organize events for different target groups from 16 to 60 years. The design should therefore be straightforward and not confused, so we are open to new colors and the logo may also be changed. In general, however, the most interesting suggestions are the most interesting ones. after this order we are looking for more graphics for quellvanto facebook instagramm homepage etc A new design is due for the new headquarters and the new challenges. We organize events for different target groups from 16 to 60 years. The design should therefore be straightforward and not confused, so we are open to new colors and the logo may also be changed. In general, however, the most interesting suggestions are the most interesting ones. after this order we are looking for more graphics for quellvanto facebook instagramm homepage etc
Updates

Reason: I am sorry for this decision but i need some more time. No new designs please, there are so many good ones and I will have made a decision in the next 3 days.

Target Market(s)

Industry/Entity Type

Business

Font styles to use
Serif
Sans Serif

Colors

Designer to choose colors to be used in the design.

Requirements
Must have
Nice to have
Should not have

```html
<!DOCTYPE html>
<html lang="en">
<head>
<meta charset="UTF-8">
<title>quellvanto business card</title>
<link rel="stylesheet" href="https://fonts.googleapis.com/css2?family=Lato:wght@300;400&display=swap">
<style>
  :root {
    --stage: #2e2e2e;
    --brand-red: #c02a3c;
    --card-black: #161616;
    --text-grey: #8a8a8a;
    --text-light: #f2f2f2;
    --accent-red: #c4283b;
  }
  html, body {
    margin: 0;
    padding: 0;
    width: 1200px;
    height: 900px;
    overflow: hidden;
    background: var(--stage);
    font-family: "Lato", sans-serif;
  }
  .canvas {
    width: 1200px;
    height: 900px;
    display: flex;
    flex-direction: column;
    align-items: center;
    justify-content: center;
    gap: 60px;
  }
  .card {
    width: 600px;
    height: 343px;
    border-radius: 24px;
    position: relative;
    overflow: hidden;
    box-shadow: 0 10px 30px rgba(0,0,0,0.45);
  }
  .card--front { background: var(--brand-red); }
  .card--back { background: var(--card-black); }
  .wordmark {
    position: absolute;
    font-weight: 400;
    letter-spacing: 0.5px;
    line-height: 1;
    white-space: nowrap;
  }
  .card--front .wordmark {
    right: 60px;
    top: 140px;
    font-size: 56px;
    color: var(--text-light);
  }
  .card--back .wordmark {
    left: 44px;
    top: 172px;
    font-size: 44px;
    color: var(--text-grey);
  }
  .divider {
    position: absolute;
    left: 310px;
    top: 60px;
    width: 2px;
    height: 225px;
    background: var(--accent-red);
  }
  .contact {
    position: absolute;
    left: 338px;
    top: 82px;
    color: var(--text-grey);
    font-weight: 300;
  }
  .contact__name {
    font-size: 26px;
    margin: 0;
    font-weight: 300;
    line-height: 1.1;
  }
  .contact__title {
    font-size: 15px;
    color: var(--accent-red);
    margin: 3px 0 14px 22px;
  }
  .contact__list {
    list-style: none;
    margin: 0;
    padding: 0 0 0 30px;
    font-size: 17px;
  }
  .contact__item {
    display: flex;
    align-items: center;
    gap: 9px;
    margin-bottom: 9px;
    white-space: nowrap;
  }
  .contact__icon {
    width: 16px;
    height: 16px;
    flex: none;
  }
  .social-square {
    width: 14px;
    height: 14px;
    margin: 0 1px;
    background: var(--accent-red);
    flex: none;
  }
</style>
</head>
<body>
<main class="canvas">
  <section class="card card--front" aria-label="Card front">
    <span class="wordmark">quellvanto</span>
  </section>

  <section class="card card--back" aria-label="Card back">
    <span class="wordmark">quellvanto</span>
    <div class="divider"></div>
    <div class="contact">
      <h1 class="contact__name">Your Name</h1>
      <div class="contact__title">Job title</div>
      <ul class="contact__list">
        <li class="contact__item">
          <svg class="contact__icon" viewBox="0 0 16 16" aria-hidden="true">
            <path d="M2 6 Q8 1 14 6 L12 8 L10 6.5 L6 6.5 L4 8 Z" fill="var(--accent-red)"/>
            <rect x="3" y="8.5" width="10" height="5.5" rx="1" fill="var(--accent-red)"/>
          </svg>
          000 000 0000
        </li>
        <li class="contact__item">
          <svg class="contact__icon" viewBox="0 0 16 16" aria-hidden="true">
            <rect x="1" y="3.5" width="14" height="9" rx="1" fill="var(--accent-red)"/>
            <path d="M1.5 4 L8 9 L14.5 4" stroke="var(--card-black)" stroke-width="1.2" fill="none"/>
          </svg>
          youremail@xyz.com
        </li>
        <li class="contact__item">
          <svg class="contact__icon" viewBox="0 0 16 16" aria-hidden="true">
            <g fill="none" stroke="var(--text-grey)" stroke-width="1.1">
              <circle cx="8" cy="8" r="6.5"/>
              <ellipse cx="8" cy="8" rx="3" ry="6.5"/>
              <line x1="1.5" y1="8" x2="14.5" y2="8"/>
            </g>
          </svg>
          yourwebsite.com
        </li>
        <li class="contact__item">
          <span class="social-square"></span>
          /quellvanto
        </li>
      </ul>
    </div>
  </section>
</main>
</body>
</html>
```